Awesome photographers card for an awesome new business

Double sided business card Black background and silver logo in middle on one side. Details on otherside. please keep it simple

Industry/Entity Type

Photographer

Contact Information for Business Card

Gerald Fenwick
0452817360
GeraldFenwickPhotography47@mailbox.test
www.GeraldFenwickPhotography.test.au
Instagram _Gerald_fenwick

Requirements
Must have
• My logo in Silver
• please use instagram logo instead of "Instagram"

```html
<!DOCTYPE html>
<html lang="en">
<head>
<meta charset="utf-8">
<title>Gerald Fenwick Photography – Business Card</title>
<link rel="stylesheet" href="https://fonts.googleapis.com/css2?family=Marcellus&display=swap">
<style>
  :root {
    --backdrop: #1e1e1e;
    --card-light: #ffffff;
    --card-sheen: #ececee;
    --card-dark: #050505;
    --silver: #c4c5c9;
    --ink: #2a2a2a;
    --ink-soft: #3a3a3a;
    --rule: #6b6b6b;
    --icon: #555555;
  }
  * { margin: 0; padding: 0; box-sizing: border-box; }
  html, body {
    width: 1200px;
    height: 1200px;
    overflow: hidden;
    background: var(--backdrop);
  }
  .canvas {
    position: relative;
    width: 1200px;
    height: 1200px;
    font-family: "Marcellus", serif;
    color: var(--ink);
  }
  .card {
    position: absolute;
    width: 663px;
    height: 377px;
  }
  .card--details {
    left: 187px; top: 185px;
    background: linear-gradient(115deg, var(--card-light) 0%, var(--card-sheen) 35%, var(--card-light) 55%, var(--card-sheen) 80%, var(--card-light) 100%);
  }
  .card--brand {
    left: 350px; top: 640px;
    background: var(--card-dark);
    box-shadow: 0 0 0 1px #333;
  }

  .brand-mark {
    position: absolute;
    display: flex;
    align-items: center;
    justify-content: center;
    border-radius: 50%;
    text-align: center;
    line-height: 1.15;
  }
  .card--details .brand-mark {
    left: 71px; top: 105px;
    width: 166px; height: 166px;
    font-size: 22px;
    color: var(--ink);
    border: 3px solid var(--ink);
  }
  .card--brand .brand-mark {
    left: 220px; top: 76px;
    width: 224px; height: 224px;
    font-size: 29px;
    color: var(--silver);
    border: 3px solid var(--silver);
  }

  .divider {
    position: absolute;
    left: 266px; top: 113px;
    width: 1px; height: 156px;
    background: var(--rule);
  }
  .details {
    position: absolute;
    left: 289px; top: 112px;
  }
  .details__name {
    font-size: 21px;
    font-weight: 400;
    letter-spacing: 0.3px;
    text-transform: uppercase;
    color: var(--ink);
    margin-bottom: 26px;
  }
  .contact { list-style: none; font-size: 15px; color: var(--ink-soft); }
  .contact__item {
    display: flex;
    align-items: center;
    gap: 6px;
    height: 24px;
  }
  .contact__item--gap { margin-top: 16px; }
  .contact__icon { width: 11px; height: 11px; flex: none; }
</style>
</head>
<body>
<main class="canvas">

  <section class="card card--details" aria-label="Card front with contact details">
    <div class="brand-mark">Gerald<br>Fenwick</div>
    <div class="divider"></div>
    <div class="details">
      <h1 class="details__name">Gerald Fenwick</h1>
      <ul class="contact">
        <li class="contact__item">
          <svg class="contact__icon" viewBox="0 0 12 12" aria-hidden="true">
            <rect x="0.5" y="0.5" width="11" height="11" rx="1.5" fill="#555"/>
            <path d="M3 4.2c0-.8.6-1.2 1.3-1.2h3.4c.7 0 1.3.4 1.3 1.2H7.6v-.4H4.4v.4zM3.5 5.2h5l.5 3.8H3z" fill="#fff"/>
          </svg>
          <span>0452817360</span>
        </li>
        <li class="contact__item">
          <svg class="contact__icon" viewBox="0 0 12 12" aria-label="Social profile">
            <rect x="0.5" y="0.5" width="11" height="11" fill="#555"/>
          </svg>
          <span>Gerald_fenwick</span>
        </li>
        <li class="contact__item contact__item--gap">
          <svg class="contact__icon" viewBox="0 0 12 12" aria-hidden="true">
            <circle cx="6" cy="6" r="5.5" fill="#555"/>
            <g fill="none" stroke="#fff" stroke-width="0.8">
              <circle cx="6" cy="6" r="3.6"/>
              <ellipse cx="6" cy="6" rx="1.6" ry="3.6"/>
              <line x1="2.4" y1="6" x2="9.6" y2="6"/>
            </g>
          </svg>
          <span>www.GeraldFenwickPhotography.test.au</span>
        </li>
        <li class="contact__item">
          <svg class="contact__icon" viewBox="0 0 12 12" aria-hidden="true">
            <rect x="0.5" y="0.5" width="11" height="11" rx="1.5" fill="#555"/>
            <rect x="2.5" y="3.5" width="7" height="5" fill="#fff"/>
            <path d="M2.5 3.5l3.5 2.6 3.5-2.6" fill="none" stroke="#555" stroke-width="0.7"/>
          </svg>
          <span>GeraldFenwickPhotography47@mailbox.test</span>
        </li>
      </ul>
    </div>
  </section>

  <section class="card card--brand" aria-label="Card back with brand name">
    <div class="brand-mark">Gerald<br>Fenwick</div>
  </section>

</main>
</body>
</html>
```